Business card for my new company (Accounting firm)

I need a business card for my new business Brightwell Advisory and Ledger SA. Our services are accounting, tax, audit and financial management. Our customers are small companies, start-ups and new companies. The final design has to show financial security, trust and growth. Please find our logo attached to the business card. Text for the business card: Brightwell Advisory and Ledger SA Tomas Varenholt Director and Founder Certified Accountant Tel. 022 418 57 34 tv@clairevalconseil.ch www.clairevalconseil.ch Rue des Vergières 27 1201 Geneva
Target Market(s)
Our customers are small companies, start-ups and new companies.
Industry/Entity Type
Finance And Accounting
Contact Information for Business Card
Claireval Conseil et Comptes SA
Tomas Varenholt
Directeur et Fondateur
Expert-comptable diplômé
Tél. 022 418 57 34
tv@clairevalconseil.ch
www.clairevalconseil.ch
Rue des Vergières 27
1201 Genève

```html
<!DOCTYPE html>
<html lang="en">
<head>
<meta charset="utf-8">
<title>Claireval Conseil et Comptes SA – Business Card</title>
<link rel="stylesheet" href="https://fonts.googleapis.com/css2?family=Lato:wght@400;700&display=swap">
<style>
  :root {
    --surface: #2b2b2d;
    --card: #111213;
    --card-edge: #1b1c1e;
    --blue: #2aa3dc;
    --blue-deep: #1566a8;
    --blue-light: #4cc0f0;
    --white: #ffffff;
    --text-grey: #b9bcc0;
    --rule: #55585c;
  }
  * { margin: 0; padding: 0; box-sizing: border-box; }
  html, body {
    width: 1200px;
    height: 900px;
    overflow: hidden;
    background: var(--surface);
    font-family: "Lato", Arial, sans-serif;
  }
  .card {
    position: absolute;
    left: 340px;
    width: 520px;
    height: 300px;
    background: linear-gradient(160deg, var(--card-edge), var(--card));
    overflow: hidden;
  }
  .card--front { top: 110px; }
  .card--back { top: 480px; }
  .card__band {
    position: absolute;
    left: 0; right: 0; bottom: 0;
    height: 9px;
    background: linear-gradient(90deg, var(--blue-deep), var(--blue-light) 55%, var(--blue-deep));
  }

  /* Front */
  .brand {
    position: absolute;
    inset: 0 0 9px 0;
    display: flex;
    flex-direction: column;
    align-items: center;
    justify-content: center;
    gap: 22px;
  }
  .brand__mark {
    width: 46px;
    height: 46px;
    background: var(--blue);
  }
  .brand__name {
    color: var(--white);
    font-weight: 700;
    font-size: 22px;
    letter-spacing: 0.12em;
    text-transform: uppercase;
  }

  /* Back */
  .contact {
    position: absolute;
    inset: 0 0 9px 0;
    display: flex;
    flex-direction: column;
    align-items: center;
    justify-content: center;
    text-align: center;
    color: var(--text-grey);
    font-size: 15px;
    line-height: 1.25;
  }
  .contact__name {
    color: var(--blue);
    font-weight: 700;
    font-size: 17px;
    text-transform: uppercase;
    letter-spacing: 0.01em;
  }
  .contact__divider {
    display: flex;
    align-items: center;
    gap: 8px;
    width: 170px;
    margin: 6px 0 4px;
  }
  .contact__divider::before,
  .contact__divider::after {
    content: "";
    flex: 1;
    height: 1px;
    background: var(--rule);
  }
  .contact__icons { display: flex; gap: 4px; }
  .contact__icon { width: 18px; height: 18px; display: block; }
  .contact__rule {
    width: 170px;
    height: 1px;
    background: var(--rule);
    margin: 6px 0;
  }
</style>
</head>
<body>

<section class="card card--front" aria-label="Card front">
  <div class="brand">
    <div class="brand__mark"></div>
    <div class="brand__name">Claireval Conseil et Comptes</div>
  </div>
  <div class="card__band"></div>
</section>

<section class="card card--back" aria-label="Card back">
  <div class="contact">
    <p class="contact__name">Tomas Varenholt</p>
    <p class="contact__role">Director and Founder</p>
    <p class="contact__role">Certified Accountant</p>

    <div class="contact__divider">
      <div class="contact__icons">
        <svg class="contact__icon" viewBox="0 0 20 20" aria-label="Phone">
          <circle cx="10" cy="10" r="10" fill="var(--blue)"/>
          <path d="M6.5 5.5c.6-.4 1.3-.2 1.6.4l.8 1.5c.2.5.1 1-.3 1.3l-.6.5c.5 1.1 1.3 1.9 2.3 2.4l.5-.6c.3-.4.9-.5 1.3-.3l1.5.8c.6.3.8 1 .4 1.6-.7 1-1.9 1.3-3 .8-2.3-1-4-2.8-5-5-.5-1.1-.2-2.3.5-3.4z" fill="var(--card)"/>
        </svg>
        <svg class="contact__icon" viewBox="0 0 20 20" aria-label="Email">
          <circle cx="10" cy="10" r="10" fill="var(--blue)"/>
          <rect x="5" y="6.5" width="10" height="7" rx="1" fill="var(--card)"/>
          <path d="M5.5 7l4.5 3.5L14.5 7" stroke="var(--blue)" stroke-width="1" fill="none"/>
        </svg>
        <svg class="contact__icon" viewBox="0 0 20 20" aria-label="Website">
          <circle cx="10" cy="10" r="10" fill="var(--blue)"/>
          <circle cx="10" cy="10" r="5" fill="none" stroke="var(--card)" stroke-width="1.4"/>
          <path d="M5 10h10M10 5c-2 2.8-2 7.2 0 10M10 5c2 2.8 2 7.2 0 10" stroke="var(--card)" stroke-width="1.1" fill="none"/>
        </svg>
      </div>
    </div>

    <p>022 418 57 34</p>
    <p>tv@clairevalconseil.ch</p>
    <p>www.clairevalconseil.ch</p>
    <div class="contact__rule"></div>
    <p>Rue des Vergières 27</p>
    <p>1201 Geneva</p>
  </div>
  <div class="card__band"></div>
</section>

</body>
</html>
```